Business Card Design Project

We are rebranding an existing automotive collision repair business. The business is called dent haven. I have attached logo but I'm not tied to that. I want to leave this wide open.

I want this card to say we are professional, competent, cutting edge. We are focused on customers and use a lot of the latest technology to make the customer experience different. We sign customers in on iPads. Paperwork I signed electronically and updates are sent via text, email, logging on a website or as they wish. I want this innovation and image to come through in our cards

Target Market(s)

60%. Women 40% men. Age 35-60

Industry/Entity Type

Automotive

Requirements
Must have
• The card must have name, title, phone,email, cell, web page

```html
<!DOCTYPE html>
<html lang="en">
<head>
<meta charset="utf-8">
<title>Dent Haven – Business Cards</title>
<link href="https://fonts.googleapis.com/css2?family=PT+Sans:wght@400;700&display=swap" rel="stylesheet">
<style>
  :root{
    --bg:#e6e9ea;
    --card:#3b3b3c;
    --card-top:#646566;
    --card-top-dark:#4e4f50;
    --green:#8dc63f;
    --white:#ffffff;
    --text:#e9e9e9;
  }
  *{margin:0;padding:0;box-sizing:border-box}
  html,body{width:1200px;height:505px;overflow:hidden}
  body{background:var(--bg);font-family:"PT Sans",sans-serif;position:relative}

  .card{position:absolute;background:var(--card);overflow:hidden}
  .card--front{left:318px;top:92px;width:170px;height:322px}
  .card--back{left:625px;top:152px;width:321px;height:170px}

  .front__band{position:absolute;left:0;top:0;width:170px;height:150px}

  .brand{position:absolute;left:0;right:0;text-align:center}
  .brand__name{font-weight:700;color:var(--green);line-height:1;letter-spacing:.2px}
  .brand__tagline{color:var(--white);font-weight:400;text-transform:uppercase;line-height:1}

  .card--front .brand{top:48px}
  .card--front .brand__name{font-size:20px}
  .card--front .brand__tagline{font-size:4.5px;letter-spacing:1.2px;margin-top:3px}

  .card--back .brand{top:76px}
  .card--back .brand__name{font-size:28px}
  .card--back .brand__tagline{font-size:6px;letter-spacing:2px;margin-top:3px}

  .person{position:absolute;left:17px;top:167px}
  .person__name{font-size:12px;font-weight:700;color:var(--white);line-height:1.2}
  .person__title{font-size:9.5px;color:var(--green);line-height:1.3}

  .contacts{position:absolute;left:16px;top:237px;list-style:none}
  .contacts li{display:flex;align-items:center;height:14px;font-size:10px;color:var(--text)}
  .contacts svg{width:8px;height:8px;margin-right:4px;fill:var(--green);flex:none}

  .web{position:absolute;left:0;right:0;top:137px;text-align:center;font-size:10.5px;font-weight:700;color:var(--green)}
</style>
</head>
<body>

<section class="card card--front" aria-label="Card front">
  <svg class="front__band" viewBox="0 0 170 150" role="img" aria-label="Decorative grey header band with a green accent curve">
    <defs>
      <linearGradient id="bandFill" x1="0" y1="0" x2="0" y2="1">
        <stop offset="0" stop-color="var(--card-top-dark)"/>
        <stop offset="1" stop-color="var(--card-top)"/>
      </linearGradient>
    </defs>
    <path d="M0 0H170V112C150 134 120 142 80 138C45 134 20 122 0 112Z" fill="url(#bandFill)"/>
    <path d="M0 114C20 124 45 136 80 140C115 144 145 136 170 116" fill="none" stroke="var(--green)" stroke-width="3"/>
  </svg>

  <div class="brand">
    <div class="brand__name">Dent Haven</div>
    <div class="brand__tagline">Repairs done right, every time</div>
  </div>

  <div class="person">
    <div class="person__name">Mark Ellison</div>
    <div class="person__title">Managing Director</div>
  </div>

  <ul class="contacts">
    <li><svg viewBox="0 0 10 10" aria-hidden="true"><path d="M2 0.5L3.8 2.6 2.9 3.8C3.5 5 4.8 6.4 6.2 7.1L7.4 6.2 9.5 8 8.3 9.5C4.5 9 1 5.5 0.5 1.7Z"/></svg>123.4567.8910</li>
    <li><svg viewBox="0 0 10 10" aria-hidden="true"><path d="M2.5 0H7.5V10H2.5ZM3.3 1V8H6.7V1Z" fill-rule="evenodd"/></svg>123.4567.8910</li>
    <li><svg viewBox="0 0 10 10" aria-hidden="true"><path d="M2.5 0H7.5V3H2.5ZM0.5 3.5H9.5V7.5H8V6H2V7.5H0.5ZM2.5 6.5H7.5V10H2.5Z"/></svg>123.4567.8910</li>
    <li><svg viewBox="0 0 10 10" aria-hidden="true"><path d="M0.5 2H9.5V8H0.5ZM1.3 2.6L5 5.3 8.7 2.6 5 4.4Z" fill-rule="evenodd"/></svg>info@denthaven.com</li>
    <li><svg viewBox="0 0 10 10" aria-hidden="true"><path d="M5 0.5A4.5 4.5 0 1 0 5 9.5 4.5 4.5 0 1 0 5 0.5ZM1.5 4.5H8.5V5.5H1.5ZM4.5 1.2H5.5V8.8H4.5Z" fill-rule="evenodd"/></svg>www.denthaven.com</li>
  </ul>
</section>

<section class="card card--back" aria-label="Card back">
  <div class="brand">
    <div class="brand__name">Dent Haven</div>
    <div class="brand__tagline">Repairs done right, every time</div>
  </div>
  <div class="web">www.denthaven.com</div>
</section>

</body>
</html>
```